Human Resource Consulting practice needs a business card design

We need a business card design (double sided colour) for our Human Resource (HR) consulting practice in regional New South Wales, australia. Our business name is Staff Compass. We support small and medium business across the Mid North Coast of New South Wales by providing them with outsourced HR support, services and products to help them achieve compliance with workplace legislation and across all areas of the employment lifecycle from recruitment to termination and everything in between. Our corporate colours are hot pink and black. The final design should communicate professionalism, trust, people focus.
I have attached the current (old) business card for your reference.

Target Market(s)

Business owners and high level managers

Industry/Entity Type

Business

Contact Information for Business Card

Name
Title
Phone no
Mobile no
Address
PO Box
email address
website

Colors
e34197

Requirements
Must have
• Tempate for changing business card personal details including Name, position title, mobile number, email address.
• Keep current logo and colours as per attached
• Logo must be presented in 2 colours or black only not white
Nice to have
• One side logo and graphic only other side logo and personal details
Should not have
• Should not be the same as the current version (attached) but a modern interpretation.
• Does not need a busy reverse side with our list of services as per current version. I feel this is too busy.
• No photos

```html
<!DOCTYPE html>
<html lang="en">
<head>
<meta charset="utf-8">
<title>Staff Compass – Business Card</title>
<link href="https://fonts.googleapis.com/css2?family=Exo+2:wght@400;500;600&display=swap" rel="stylesheet">
<style>
  :root{
    --hot-pink:#e34197;
    --charcoal:#3a3a3a;
    --ink:#2b2b2b;
    --paper:#ffffff;
    --backdrop:#e9e9eb;
  }
  *{box-sizing:border-box;margin:0;padding:0}
  html,body{width:1200px;height:897px;overflow:hidden}
  body{background:var(--backdrop);font-family:"Exo 2",sans-serif;color:var(--ink);position:relative}
  .card{
    position:absolute;top:288px;width:520px;height:320px;
    background:var(--paper);border-radius:26px;
    box-shadow:0 6px 18px rgba(0,0,0,.12);overflow:hidden;
  }
  .card--front{left:50px}
  .card--back{left:630px}
  .card__frame{
    position:absolute;inset:14px;border:2px solid var(--hot-pink);border-radius:18px;
  }
  .accent-band{
    position:absolute;left:0;top:48px;width:250px;height:30px;
    background:var(--charcoal);border-radius:0 15px 15px 0;
  }
  .accent-tab{
    position:absolute;left:430px;top:-4px;width:48px;height:30px;
    background:var(--charcoal);border-radius:0 0 15px 15px;
  }
  .identity{position:absolute;right:46px;top:44px;text-align:right}
  .identity__name{color:var(--hot-pink);font-weight:500;font-size:19px;letter-spacing:1.5px;line-height:1.1}
  .identity__title{font-size:11.5px;letter-spacing:1.6px;margin-top:4px}
  .wordmark{display:flex;align-items:flex-end;gap:5px;font-weight:500;color:var(--ink);line-height:1;white-space:nowrap}
  .card--front .wordmark{position:absolute;right:46px;top:140px;font-size:32px}
  .card--back .wordmark{position:absolute;left:50%;top:50%;transform:translate(-50%,-50%);font-size:42px}
  .wordmark__dot{width:8px;height:8px;background:var(--hot-pink);margin-bottom:6px;flex:none}
  .card--back .wordmark__dot{width:10px;height:10px;margin-bottom:8px}
  .contact{position:absolute;left:32px;bottom:36px;font-size:10.5px;line-height:1.55}
  .contact__address{margin-bottom:10px;font-size:11px;line-height:1.5}
  .contact__row{display:flex;align-items:center;gap:7px}
  .contact__row svg{width:10px;height:10px;fill:var(--hot-pink);flex:none}
</style>
</head>
<body>
  <section class="card card--front">
    <div class="card__frame"></div>
    <div class="accent-band"></div>
    <div class="accent-tab"></div>

    <div class="identity">
      <p class="identity__name">CLAIRE DAWSON</p>
      <p class="identity__title">GENERAL MANAGER</p>
    </div>

    <div class="wordmark"><span>Staff Compass</span><span class="wordmark__dot"></span></div>

    <div class="contact">
      <p class="contact__address">14 Harbour View Road,<br>Level 2, Riverside</p>
      <p class="contact__row"><svg viewBox="0 0 10 10"><path d="M2 0.5 3.8 2.6 2.9 3.8C3.6 5.2 4.8 6.4 6.2 7.1L7.4 6.2 9.5 8 8.6 9.5C4.5 9.2 0.8 5.5 0.5 1.4Z"/></svg>02 6550 4812</p>
      <p class="contact__row"><svg viewBox="0 0 10 10"><path d="M2.5 0h5a1 1 0 0 1 1 1v8a1 1 0 0 1-1 1h-5a1 1 0 0 1-1-1V1a1 1 0 0 1 1-1Zm.5 1.5v6h4v-6Z"/></svg>0412 550 481</p>
      <p class="contact__row"><svg viewBox="0 0 10 10"><path d="M2 0h5v3H2Zm-1 3.5h8a1 1 0 0 1 1 1V9H0V4.5a1 1 0 0 1 1-1Z"/></svg>02 6550 4813</p>
      <p class="contact__row"><svg viewBox="0 0 10 10"><path d="M0 1.5h10v7H0Zm1 1 4 3 4-3v-.2H1Z"/></svg>hello@staffcompass.au</p>
      <p class="contact__row"><svg viewBox="0 0 10 10"><circle cx="5" cy="5" r="5"/><path d="M0.5 5h9M5 0.5v9" stroke="#fff" stroke-width=".8"/></svg>www.staffcompass.au</p>
    </div>
  </section>

  <section class="card card--back">
    <div class="card__frame"></div>
    <div class="wordmark"><span>Staff Compass</span><span class="wordmark__dot"></span></div>
  </section>
</body>
</html>
```